Visitenkarten-Design für Garten- und Landschaftspflege
Nerapo Kulm setzte meine Vorstellungen absolut super um ich kann Ihn nur weiter empfehlen. vielen dank
Zielgruppe
Baumpflege, Baumfällung, Garten und Landschaftspflege meine zielgruppe sind Privatpersonen im alter von 20-100Jahren
Aufgabenstellung
Sehr geehrte Damen und Herren, die visitenkarte sollte die angaben so enthalten wie sie auf der von mir gestallteten Visitenkarten sind ( meine ist kein maß der Dinge). Ich habe mein Logo leider nur als 3.jpg Datei. Das Logo darf im Design erändert werden aber bitte nur Feinheiten ansonsten stehen ihnen alle türen offen um kreativ zu sein.
mit freundlichen Grüßen Jonas Vehmar

```html
<!DOCTYPE html>
<html lang="de">
<head>
<meta charset="utf-8">
<title>Visitenkarte Baumpflege Vehmar</title>
<link href="https://fonts.googleapis.com/css2?family=Fira+Sans:wght@400;500;700&display=swap" rel="stylesheet">
<style>
  :root {
    --page: #ffffff;
    --card-green: #9aba3d;
    --card-green-deep: #87a736;
    --ink: #0a0a06;
    --shadow: rgba(0, 0, 0, 0.22);
  }
  html, body {
    margin: 0;
    padding: 0;
    width: 1200px;
    height: 840px;
    overflow: hidden;
    background: var(--page);
    font-family: "Fira Sans", Arial, sans-serif;
    color: var(--ink);
  }
  .canvas {
    position: relative;
    width: 1200px;
    height: 840px;
  }
  .card {
    position: absolute;
    top: 150px;
    width: 331px;
    height: 511px;
    background: var(--card-green);
    box-shadow: 5px 5px 6px var(--shadow);
    overflow: hidden;
  }
  .card--front { left: 243px; }
  .card--back { left: 639px; }

  .card__texture {
    position: absolute;
    inset: 0;
    background: linear-gradient(160deg, var(--card-green) 0%, var(--card-green) 30%, var(--card-green-deep) 62%, var(--card-green) 100%);
  }

  .brand {
    position: absolute;
    left: 32px;
    width: 267px;
    top: 60px;
  }
  .brand__dot {
    width: 64px;
    height: 64px;
    margin: 0 auto;
    border-radius: 50%;
    background: var(--ink);
  }
  .brand__name {
    position: absolute;
    top: 95px;
    left: -4px;
    right: -4px;
    text-align: center;
    font-weight: 700;
    font-size: 21px;
    line-height: 24px;
    letter-spacing: 0.17em;
    white-space: nowrap;
    text-indent: 0.17em;
  }
  .brand__rule {
    position: absolute;
    top: 133px;
    left: 0;
    width: 267px;
    height: 2px;
    background: var(--ink);
  }

  .contact {
    position: absolute;
    left: 30px;
    top: 257px;
    margin: 0;
    font-style: normal;
    font-size: 17px;
    line-height: 23.3px;
    font-weight: 400;
    white-space: nowrap;
  }
  .contact__name { font-weight: 700; }
  .contact__gap { height: 23.3px; }

  .services {
    position: absolute;
    left: 31px;
    top: 287px;
    width: 250px;
  }
  .services__title {
    margin: 0;
    font-size: 21px;
    font-weight: 700;
    letter-spacing: 0.17em;
    white-space: nowrap;
    line-height: 24px;
  }
  .rule {
    height: 2px;
    background: var(--ink);
  }
  .services__title + .rule { margin-top: 4px; }
  .services__list {
    list-style: none;
    margin: 6px 0 0;
    padding: 0;
    font-size: 17px;
    font-weight: 400;
    line-height: 21px;
    white-space: nowrap;
  }
  .services__list li::before { content: "• "; }
  .services__list + .rule { margin-top: 13px; }
  .services__extra {
    margin: 9px 0 0;
    font-size: 16.5px;
    font-weight: 400;
    line-height: 20.5px;
    white-space: nowrap;
  }
</style>
</head>
<body>
<div class="canvas">
  <section class="card card--front">
    <div class="brand">
      <div class="brand__dot"></div>
      <div class="brand__name">BAUMPFLEGE VEHMAR</div>
      <div class="brand__rule"></div>
    </div>
    <address class="contact">
      <div class="contact__name">Jonas Vehmar</div>
      <div>Fachagrarwirt</div>
      <div>Baumpflege/Baumsanierung</div>
      <div class="contact__gap"></div>
      <div>Lindenweg 7</div>
      <div>84123 Moosbrunn</div>
      <div>0170 48291537</div>
      <div>www.baumpflege-vehmar.de</div>
      <div>kontakt@baumpflege-vehmar.de</div>
    </address>
  </section>

  <section class="card card--back">
    <div class="card__texture" role="img" aria-label="Dezente Baumkronen-Textur in dunklerem Grün"></div>
    <div class="brand">
      <div class="brand__dot"></div>
      <div class="brand__name">BAUMPFLEGE VEHMAR</div>
      <div class="brand__rule"></div>
    </div>
    <div class="services">
      <h2 class="services__title">UNSERE LEISTUNGEN</h2>
      <div class="rule"></div>
      <ul class="services__list">
        <li>Beratung und Baumgutachten</li>
        <li>Kronenpflege &amp; Einkürzung</li>
        <li>Baumfällung</li>
        <li>Obstbaumschnitt</li>
      </ul>
      <div class="rule"></div>
      <p class="services__extra">Aufbau &amp; Anfertigung von<br>Gartenhäusern nach Maß</p>
    </div>
  </section>
</div>
</body>
</html>
```